Marlow Vale Stud website

We would like to create a horse stud/agistment farm website similar to this websites we have attached below:
www.thornbeck.com.au
www.quillstead.com.au
www.brackley.com
www.pimsey.com.au
The main colour scheme are purple and white to align with the stable's racing colours.
We have also attach the company logo and also images of the farm and create some ideas for the website.
Many thanks for looking into this project!

```html
<!DOCTYPE html>
<html lang="en">
<head>
<meta charset="utf-8">
<title>Marlow Vale Stud</title>
<link rel="stylesheet" href="https://fonts.googleapis.com/css2?family=Crimson+Text:wght@400;700&family=Montserrat:wght@400;500;700&display=swap">
<style>
:root{
  --purple:#4a2353;
  --purple-deep:#3a1a42;
  --purple-pill:#5b2a6a;
  --dark:#232323;
  --darker:#1c1c1c;
  --white:#ffffff;
  --muted:#8d8d8d;
  --muted-light:#c9bccd;
  --serif:"Crimson Text", Georgia, serif;
  --sans:"Montserrat", Arial, sans-serif;
}
*{margin:0;padding:0;box-sizing:border-box}
html,body{width:1200px;height:4276px;overflow:hidden}
body{position:relative;background:var(--dark);font-family:var(--sans);color:var(--white)}
.abs{position:absolute}
ul{list-style:none}

/* hero */
.hero{left:0;top:0;width:1200px;height:678px;background:linear-gradient(100deg,#4e4034 0%,#6b4b35 35%,#8a5634 60%,#5a3c2a 85%,#3a2b22 100%)}
.hero-shade{left:0;top:0;width:1200px;height:678px;background:linear-gradient(180deg,rgba(20,15,20,.35),rgba(60,30,60,.35))}
.brand-top{left:78px;top:32px;display:flex;align-items:center;gap:10px;font-family:var(--serif);font-size:26px;font-weight:700}
.brand-dot{width:14px;height:14px;border-radius:50%;background:var(--white)}
.nav{right:70px;top:36px;display:flex;align-items:center;gap:22px;font-size:15px}
.nav .active{background:var(--purple-pill);padding:9px 24px;border-radius:20px}
.hero-title{left:0;top:262px;width:1200px;text-align:center;font-size:74px;font-weight:700;line-height:80px}
.hero-sub{left:0;top:436px;width:1200px;text-align:center;font-size:25px}

/* section headers */
.section-head{left:0;width:1200px;height:208px;background:var(--dark)}
.head-mark{left:208px;top:40px;width:110px;height:110px;border-radius:50%;background:#2d2d2d}
.head-title{left:345px;font-family:var(--serif);font-weight:700;font-size:32px;letter-spacing:1px}
.head-text{left:345px;width:700px;font-size:15px;line-height:28px;color:var(--muted)}

/* stallions */
.stallion-photo{left:0;top:886px;width:678px;height:627px;background:linear-gradient(180deg,#6f9bd0 0%,#a8c6e4 40%,#5f8a3e 55%,#3f6a2a 100%)}
.stallion-caption{left:80px;top:1410px;font-family:var(--serif);font-weight:700;font-size:42px}
.stallion-caption-sub{left:80px;top:1468px;font-size:15px}
.stallion-strip{left:678px;top:886px;width:68px;height:627px;background:var(--purple-deep)}
.stallion-panel{left:746px;top:886px;width:454px;height:627px;background:var(--purple)}
.panel-title{left:820px;top:958px;font-family:var(--serif);font-weight:700;font-size:46px;letter-spacing:1px}
.stallion-list{left:826px;top:1050px;font-family:var(--serif);font-size:22px;line-height:57px}
.stallion-list .current{font-weight:700;text-decoration:underline}

/* news */
.news{left:0;top:1721px;width:1200px;height:898px;background:linear-gradient(180deg,#4a2555,#40204b 60%,#4a2a52)}
.news-item{left:194px;width:818px;height:231px}
.news-img{left:0;top:0;width:313px;height:231px}
.news-body{left:347px;top:8px;width:471px}
.news-title{font-family:var(--serif);font-weight:700;font-size:24px;line-height:32px}
.news-text{margin-top:14px;font-size:14px;line-height:27px;color:var(--muted-light)}
.news-date{margin-top:12px;display:flex;align-items:center;gap:10px;font-size:13px;font-weight:500}
.news-rule{left:541px;width:471px;height:1px;background:rgba(255,255,255,.2)}

/* gallery */
.gallery{left:0;top:2827px;width:1200px;height:556px;background:linear-gradient(180deg,#4a5560 0%,#7d8890 40%,#6b7a5c 62%,#4f5e3c 100%)}
.arrow{width:48px;height:48px;border-radius:50%;border:2px solid rgba(255,255,255,.7);top:3063px}
.social{left:0;top:3383px;width:1200px;height:154px;background:var(--purple)}
.social-dot{top:3437px;width:46px;height:46px;border-radius:50%;border:3px solid var(--white)}
.tile{top:3537px;width:300px;height:333px}

/* footer */
.footer{left:0;top:3870px;width:1200px;height:342px;background:var(--darker)}
.foot-brand{left:77px;top:3918px;display:flex;align-items:center;gap:12px;font-family:var(--serif);font-weight:700;font-size:28px}
.foot-contact{left:77px;top:3988px;font-size:13px;line-height:20px;width:240px}
.foot-row{display:flex;gap:14px;align-items:flex-start;margin-bottom:20px}
.foot-row svg{flex:none;margin-top:2px}
.foot-social{left:77px;top:4138px;display:flex;gap:12px}
.foot-social span{width:38px;height:38px;border-radius:50%;background:#1b6fb5}
.foot-head{top:3916px;font-family:var(--serif);font-weight:700;font-size:22px;letter-spacing:.5px}
.foot-list{top:3956px;font-size:14px;line-height:29px;color:#cfcfcf}
.foot-list li::before{content:"›";margin-right:10px;color:var(--muted)}
.newsletter-text{left:883px;top:3956px;width:250px;font-size:14px;line-height:24px}
.email-box{left:883px;top:4036px;width:240px;height:44px;background:var(--white);color:#888;font-size:13px;padding:13px 14px}
.email-btn{left:1076px;top:4036px;width:47px;height:44px;background:var(--purple);display:flex;align-items:center;justify-content:center}
.subscribe{left:883px;top:4095px;width:140px;height:42px;border-radius:21px;background:var(--purple-pill);font-family:var(--serif);font-weight:700;font-size:17px;display:flex;align-items:center;justify-content:center}
.copyright{left:0;top:4212px;width:1200px;height:64px;background:var(--purple-deep);text-align:center;font-size:13px;line-height:64px;color:#d8cbdc}
</style>
</head>
<body>

<header>
  <div class="abs hero" role="img" aria-label="Photograph of a chestnut horse's head near a paddock fence"></div>
  <div class="abs hero-shade"></div>
  <div class="abs brand-top"><span class="brand-dot"></span>Marlow Vale</div>
  <nav class="abs nav">
    <span class="active">Home</span><span>Stallions</span><span>News</span><span>Sales</span><span>Gallery</span><span>About</span><span>Contact</span>
    <svg width="16" height="16" viewBox="0 0 16 16"><circle cx="6.5" cy="6.5" r="5" fill="none" stroke="#fff" stroke-width="2"/><line x1="10.5" y1="10.5" x2="15" y2="15" stroke="#fff" stroke-width="2.4"/></svg>
  </nav>
  <h1 class="abs hero-title">Our kingdom For<br>A Horse</h1>
  <p class="abs hero-sub">Inter Relation Between Horse &amp; Rider</p>
</header>

<section>
  <div class="abs section-head" style="top:678px"></div>
  <div class="abs head-mark" style="top:718px"></div>
  <h2 class="abs head-title" style="top:734px">WELCOME TO MARLOW VALE</h2>
  <p class="abs head-text" style="top:784px">Lorem Ipsum is simply dummy text of the printing and typesetting industry. Lorem Ipsum has been the industry's standard dummy text ever since the when an unknown.</p>
</section>

<section>
  <div class="abs stallion-photo" role="img" aria-label="Photograph of a jockey in purple silks riding a grey racehorse across green grass"></div>
  <h3 class="abs stallion-caption">Riverstone</h3>
  <p class="abs stallion-caption-sub">Lorem Ipsum is simply dummy text of the printing and typesetting</p>
  <div class="abs stallion-strip"></div>
  <div class="abs stallion-panel"></div>
  <h2 class="abs panel-title">STALLIONS</h2>
  <ul class="abs stallion-list">
    <li>Far Too Bold</li><li>Harbour Prince</li><li class="current">Riverstone</li><li>Ever So Ready</li><li>Pluckley</li><li>Press Release</li><li>Star Gazer</li>
  </ul>
</section>

<section>
  <div class="abs section-head" style="top:1513px"></div>
  <div class="abs head-mark" style="top:1553px"></div>
  <h2 class="abs head-title" style="top:1564px">NEWS</h2>
  <p class="abs head-text" style="top:1614px">Lorem Ipsum is simply dummy text of the printing and typesetting industry. Lorem Ipsum has been the industry's standard dummy text ever since the when an unknown.</p>

  <div class="abs news"></div>

  <article class="abs news-item" style="top:1784px">
    <div class="abs news-img" style="background:linear-gradient(180deg,#a7b1a8 0%,#7f8b76 40%,#4f7a33 70%,#3e6a27 100%)" role="img" aria-label="Photograph of a white horse grazing in a field"></div>
    <div class="abs news-body">
      <h3 class="news-title">Lorem Ipsum is simply dummy text of the printing and.</h3>
      <p class="news-text">Lorem Ipsum is simply dummy text of the printing and typesetting industry. Lorem Ipsum has been the industry's standard dummy text ever since the when an unknown printer took.</p>
      <p class="news-date"><svg width="14" height="14" viewBox="0 0 14 14"><rect x="1" y="2.5" width="12" height="10.5" fill="none" stroke="#fff" stroke-width="1.6"/><rect x="1" y="2.5" width="12" height="3" fill="#fff"/></svg>07 March 2019</p>
    </div>
  </article>
  <div class="abs news-rule" style="top:2016px"></div>

  <article class="abs news-item" style="top:2046px">
    <div class="abs news-img" style="background:linear-gradient(160deg,#8fb2d6 0%,#9c7a5a 45%,#6a5a4c 70%,#4a6a35 100%)" role="img" aria-label="Photograph of three horses standing together"></div>
    <div class="abs news-body">
      <h3 class="news-title">Lorem Ipsum is simply dummy text of the printing and.</h3>
      <p class="news-text">Lorem Ipsum is simply dummy text of the printing and typesetting industry. Lorem Ipsum has been the industry's standard dummy text ever since the when an unknown printer took.</p>
      <p class="news-date"><svg width="14" height="14" viewBox="0 0 14 14"><rect x="1" y="2.5" width="12" height="10.5" fill="none" stroke="#fff" stroke-width="1.6"/><rect x="1" y="2.5" width="12" height="3" fill="#fff"/></svg>07 March 2019</p>
    </div>
  </article>
  <div class="abs news-rule" style="top:2278px"></div>

  <article class="abs news-item" style="top:2308px">
    <div class="abs news-img" style="background:linear-gradient(180deg,#9fc2e2 0%,#c8d9e6 30%,#6f8f5a 55%,#4b6e33 100%)" role="img" aria-label="Aerial photograph of the stud farm and its paddocks"></div>
    <div class="abs news-body">
      <h3 class="news-title">Lorem Ipsum is simply dummy text of the printing and.</h3>
      <p class="news-text">Lorem Ipsum is simply dummy text of the printing and typesetting industry. Lorem Ipsum has been the industry's standard dummy text ever since the when an unknown printer took.</p>
      <p class="news-date"><svg width="14" height="14" viewBox="0 0 14 14"><rect x="1" y="2.5" width="12" height="10.5" fill="none" stroke="#fff" stroke-width="1.6"/><rect x="1" y="2.5" width="12" height="3" fill="#fff"/></svg>07 March 2019</p>
    </div>
  </article>
</section>

<section>
  <div class="abs section-head" style="top:2619px"></div>
  <div class="abs head-mark" style="top:2659px"></div>
  <h2 class="abs head-title" style="top:2672px">OUR GALLERY</h2>
  <p class="abs head-text" style="top:2722px">Lorem Ipsum is simply dummy text of the printing and typesetting industry.</p>

  <div class="abs gallery" role="img" aria-label="Photograph of three ponies standing on a grassy hill under a cloudy sky"></div>
  <div class="abs arrow" style="left:13px"><svg width="44" height="44" viewBox="0 0 44 44"><polyline points="25,15 18,22 25,29" fill="none" stroke="#fff" stroke-width="2"/></svg></div>
  <div class="abs arrow" style="left:1139px"><svg width="44" height="44" viewBox="0 0 44 44"><polyline points="19,15 26,22 19,29" fill="none" stroke="#fff" stroke-width="2"/></svg></div>

  <div class="abs social"></div>
  <span class="abs social-dot" style="left:484px"></span>
  <span class="abs social-dot" style="left:564px"></span>
  <span class="abs social-dot" style="left:658px"></span>

  <div class="abs tile" style="left:0;background:linear-gradient(135deg,#e9c27a,#b5622c 55%,#6e3b1e)" role="img" aria-label="Photograph of a chestnut horse with flowing mane"></div>
  <div class="abs tile" style="left:300px;background:linear-gradient(180deg,#7a7470,#4a3a32 60%,#2f2a28)" role="img" aria-label="Photograph of a dark bay horse's head"></div>
  <div class="abs tile" style="left:600px;background:linear-gradient(180deg,#8a8c8e,#5a4636 55%,#3b2f27)" role="img" aria-label="Photograph of a brown horse galloping"></div>
  <div class="abs tile" style="left:900px;background:linear-gradient(180deg,#3f4a3a,#6a6a52 45%,#3a5a2a)" role="img" aria-label="Photograph of a horse standing near trees"></div>
</section>

<footer>
  <div class="abs footer"></div>
  <div class="abs foot-brand"><span class="brand-dot"></span>Marlow Vale</div>
  <div class="abs foot-contact">
    <div class="foot-row"><svg width="14" height="18" viewBox="0 0 14 18"><path d="M7 1a6 6 0 0 1 6 6c0 4.5-6 10-6 10S1 11.5 1 7a6 6 0 0 1 6-6z" fill="#6a3a7a"/><circle cx="7" cy="7" r="2.2" fill="#1c1c1c"/></svg><span>101 - Lorem ipsum simple text of print and type industry.</span></div>
    <div class="foot-row"><svg width="14" height="16" viewBox="0 0 14 16"><path d="M3 1l3 3-2 2c1 2 3 4 5 5l2-2 3 3-2 3C6 15 0 8 1 3z" fill="#6a3a7a"/></svg><span>123 456 7890</span></div>
    <div class="foot-row"><svg width="16" height="12" viewBox="0 0 16 12"><rect width="16" height="12" fill="#6a3a7a"/><polyline points="0,0 8,7 16,0" fill="none" stroke="#1c1c1c" stroke-width="1.5"/></svg><span>info@marlowvale.com</span></div>
  </div>
  <div class="abs foot-social"><span></span><span style="background:#2aa3e0"></span><span style="background:#2f7fc1"></span></div>

  <h4 class="abs foot-head" style="left:350px">SITEMAP</h4>
  <ul class="abs foot-list" style="left:350px"><li>Home</li><li>Stallions</li><li>News</li><li>Sales</li><li>Gallery</li><li>About</li><li>Contact</li></ul>

  <h4 class="abs foot-head" style="left:621px">STALLIONS</h4>
  <ul class="abs foot-list" style="left:621px"><li>Far Too Bold</li><li>Harbour Prince</li><li>Riverstone</li><li>Ever So Ready</li><li>Pluckley</li><li>Press Release</li><li>Star Gazer</li></ul>

  <h4 class="abs foot-head" style="left:883px">NEWSLETTER</h4>
  <p class="abs newsletter-text">Would you like to receive our exclusive news and updates for sign up our newsletter !</p>
  <div class="abs email-box">Enter Email *</div>
  <div class="abs email-btn"><svg width="16" height="12" viewBox="0 0 16 12"><rect width="16" height="12" fill="#fff"/><polyline points="0,0 8,7 16,0" fill="none" stroke="#4a2353" stroke-width="1.5"/></svg></div>
  <div class="abs subscribe">SUBSCRIBE</div>

  <div class="abs copyright">©Marlow Vale -2019-All right Reserved</div>
</footer>

</body>
</html>
```